Heron Loan Partners Business Card

We need a business card design for our mortgage servicing company. In addition to servicing the loans of homeowners, we help homeowners with purchasing their homes and any mortgage refinancing. We would like to see designs that use the colors in the logo attached below (gold-ish yellow and navy blue), and any other design you deem fit! The design should communicate a simpler life with smart mortgages provided by Heron.

```html
<!DOCTYPE html>
<html lang="en">
<head>
<meta charset="utf-8">
<title>Heron Loan Partners – Business Card</title>
<link href="https://fonts.googleapis.com/css2?family=Arimo:wght@400;700&family=Tinos:wght@400;700&display=swap" rel="stylesheet">
<style>
  :root {
    --navy: #282154;
    --gold: #e0b03e;
    --white: #ffffff;
    --ink: #111111;
    --rule: #9a9a9a;
    --backdrop: #2b2b2b;
  }
  * { box-sizing: border-box; margin: 0; padding: 0; }
  html, body {
    width: 1200px; height: 1040px; overflow: hidden;
    background: var(--backdrop);
  }
  .sheet {
    width: 1200px; height: 1040px;
    display: flex; flex-direction: column; align-items: center; justify-content: center;
    gap: 40px;
  }
  .card {
    width: 840px; height: 480px;
    border-radius: 0 70px 0 70px;
    position: relative;
    overflow: hidden;
  }
  .card--back { background: var(--navy); display: flex; align-items: center; justify-content: center; }
  .card--front { background: var(--white); display: flex; align-items: center; }

  .wordmark {
    display: flex; align-items: center; gap: 16px;
    font-family: "Tinos", serif; font-weight: 700;
    color: var(--gold); line-height: 1;
  }
  .wordmark__dot { border-radius: 50%; background: var(--gold); }
  .card--back .wordmark { font-size: 120px; }
  .card--back .wordmark__dot { width: 30px; height: 30px; }
  .card--front .wordmark { font-size: 82px; }
  .card--front .wordmark__dot { width: 22px; height: 22px; }

  .front__brand { width: 50%; display: flex; justify-content: center; }
  .front__divider { width: 1px; height: 250px; background: var(--rule); }
  .front__details { padding-left: 34px; font-family: "Arimo", sans-serif; color: var(--ink); }

  .person__name { font-family: "Tinos", serif; font-size: 40px; line-height: 1; }
  .person__first { color: var(--gold); }
  .person__last { color: var(--navy); font-weight: 700; }
  .person__role { font-size: 24px; margin-top: 4px; margin-bottom: 20px; }

  .contact { list-style: none; font-size: 24px; line-height: 1.45; }
  .contact li { display: flex; align-items: center; gap: 10px; }
  .contact svg { width: 22px; height: 22px; flex: none; }
  .contact .accent { color: var(--gold); }
  .address { font-size: 24px; line-height: 1.3; margin-top: 14px; }
</style>
</head>
<body>
<main class="sheet">
  <section class="card card--back" aria-label="Card back">
    <div class="wordmark"><span class="wordmark__dot"></span>Heron</div>
  </section>

  <section class="card card--front" aria-label="Card front">
    <div class="front__brand">
      <div class="wordmark"><span class="wordmark__dot"></span>Heron</div>
    </div>
    <div class="front__divider"></div>
    <div class="front__details">
      <p class="person__name"><span class="person__first">Daniel</span> <span class="person__last">Porter</span></p>
      <p class="person__role">Managing Director</p>
      <ul class="contact">
        <li>
          <svg viewBox="0 0 24 24" fill="none" stroke="#e0b03e" stroke-width="2"><path d="M5 3h4l2 5-2.5 1.5a11 11 0 0 0 6 6L16 13l5 2v4a2 2 0 0 1-2 2A17 17 0 0 1 3 5a2 2 0 0 1 2-2z"/></svg>
          044-555 210 347
        </li>
        <li>
          <svg viewBox="0 0 24 24" fill="#e0b03e"><path d="M2 5h20v14H2z"/><path d="M2 5l10 8 10-8" stroke="#fff" stroke-width="1.6" fill="none"/></svg>
          info@heronloan.com
        </li>
        <li>
          <svg viewBox="0 0 24 24" fill="none" stroke="#e0b03e" stroke-width="1.8"><circle cx="12" cy="12" r="9"/><path d="M3 12h18M12 3c3 3 3 15 0 18M12 3c-3 3-3 15 0 18"/></svg>
          <span>www.<span class="accent">heronloanpartners</span>.com</span>
        </li>
      </ul>
      <p class="address">18 Harbour View Road<br>45120, Northbay</p>
    </div>
  </section>
</main>
</body>
</html>
```